Doctor to Patient Management Website

I need a design for a health management website that connects doctors to patients. The website will consist of: A main page mainly describing our goal, services, and initiatives towards (Who we are AKA "About Us", Our services, Contact Us, Quick Links for health tips, Language selection, Find a doctor, search bar, Member Login Section, small glossary section below with links to all entities mentioned prior, Help section (Helpful tips and tutorials, Used to request help from admin, customer service, to resolve issues or get assistance). A profile page with two types:1) Doctor Profile: Doctor Personal info (First, Last, Middle Name, Title), Clinic, Hospital Info, Department, Credentials, Years of Experience, Patients rating, #Patients seen during the current week, #Patients seen in total, Picture, Link to email doctor, Link to print doctor's profile). Tabs for "About Me", "Contact Info", "Ratings & Comments", "Documents" (To be downloaded and uploaded by patient), "Patients (List of Patients alphabetical order by name)", "Calendar" (to see doctor's availability for booking) underneath all links. 2) Patient profile: About me, Personal Info, Height, Weight, Blood Type, Age, DOB, Name, etc..., Message and email link.Picture of patient with menu made of "Personal Data", "Biometrics", "Allergies", "Illnesses", "Medications", "Medical Procedures", "Doctors" treating the patient, "Documents" (To be downloaded and uploaded by patient). Underneath all, other patients he or she is related to (For example: family member, so patient can't connect to other patients who are family members)3) Login section: New Users will have option to register using:First Name (Required), Last Name, Middle (not required), Address (Not required), City (Required), Country (Required), Email (Not required), Phone Number (Required), Choose UserName, Password, Account Type (Doctor or Patient). Once registered, they will log in using UserName, Password, and Account_Type.Curent Users will log in using UserName, Password, and Account_Type and option to retrieve username or password.Pages to include (Login Page - Registration Page - Retrieve Username and Reset Password Page)Please see link below:https://plumcrate-adwerks.net/importance-claiming-vantorix-quibble-zarn/Pictures are attached to this project as an inspirationFYI: Dummy text can be used to fill in the business, services, and descriptive information. Feel free to include your own ideas in the layout, design, categories, patterns, and more to and showcase your talent. Design and pictures provided are available as source of ideas.

Target Market(s)

Age: 21+ / Family Oriented / Medical Sector / Metropolitan Area / Educated and non Educated Users

Industry/Entity Type

Health Care

Number of Pages Required

5+ page

Font styles to use
Sans Serif

Colors

Designer to choose colors to be used in the design.

Requirements
Must have
• Thin layer design
• Simple font - No serif
• Clean menu with light but solid colors (No Gradient effect)
Nice to have
• Different color themes (2 or 3) can be combined
• Sample pictures for illustration (either as an ad or to go with the flow of your design)
• Dashboard Feel (Suggested but not required)
Should not have
• Artistic fonts - with Serif
• Dark color themes

```html
<!DOCTYPE html>
<html lang="en">
<head>
<meta charset="utf-8">
<title>Velmora — Doctor to Patient Care</title>
<link href="https://fonts.googleapis.com/css2?family=Poppins:wght@400;500;600;700&family=Roboto:ital,wght@0,400;0,500;0,700;1,400&display=swap" rel="stylesheet">
<style>
:root{
  --red:#f2100f;
  --ink:#111111;
  --white:#ffffff;
  --soft:#f3f3f3;
  --dark:#141618;
  --footer:#1a1c1e;
  --muted:#cfcfcf;
}
*{box-sizing:border-box;margin:0;padding:0}
html,body{width:1200px;height:3991px;overflow:hidden}
body{position:relative;font-family:"Roboto",Arial,sans-serif;color:var(--ink);background:var(--white)}
.abs{position:absolute}
.brand{display:flex;align-items:center;gap:16px;color:var(--white);font-family:"Poppins",Arial,sans-serif;font-weight:700;font-size:44px;line-height:1;z-index:4}
.brand-dot{width:40px;height:40px;border-radius:50%;background:var(--white)}
.brand-top{left:100px;top:38px}
.brand-footer{left:0;top:3490px;width:1200px;justify-content:center}

/* hero */
.hero{left:0;top:0;width:1200px;height:673px;background:linear-gradient(100deg,#4a4c4e 0%,#6f6c69 45%,#8d8780 75%,#a39b92 100%)}
.hero-shade{left:0;top:0;width:1200px;height:673px;background:rgba(20,20,22,.35)}
.lang{left:872px;top:42px;display:flex;align-items:center;gap:10px}
.lang-flag{width:34px;height:24px;background:#2b3f8f;border:2px solid #fff}
.login-btn{left:979px;top:37px;width:125px;height:35px;background:var(--red);color:#fff;border-radius:4px;font-size:14px;display:flex;align-items:center;justify-content:center}
.nav{left:0;top:152px;width:1200px;display:flex;justify-content:center;gap:52px;font-family:"Poppins",Arial,sans-serif;font-weight:600;font-size:18px;color:#fff}
.hero-title{left:0;top:270px;width:1200px;text-align:center;font-family:"Poppins",Arial,sans-serif;font-weight:700;font-size:58px;color:#fff}
.hero-sub{left:310px;top:366px;width:580px;text-align:center;font-size:17px;line-height:27px;color:#fff}
.search{left:333px;top:458px;width:513px;height:50px;background:#fff;border-radius:4px;display:flex;align-items:center;padding-left:16px}
.search span{color:#888;font-size:17px}
.search-btn{right:4px;top:4px;width:138px;height:42px;background:var(--red);color:#fff;font-size:19px;display:flex;align-items:center;justify-content:center;border-radius:3px}

/* about */
.about-photo{left:80px;top:718px;width:360px;height:394px;background:linear-gradient(180deg,#eef1f4 0%,#d8dfe6 60%,#f6f7f8 100%)}
.h-red{font-family:"Poppins",Arial,sans-serif;font-weight:700;color:var(--red);font-size:42px}
.body-text{font-size:15px;line-height:28px;color:#111}
.btn-red{background:var(--red);color:#fff;border-radius:6px;font-size:15px;display:flex;align-items:center;justify-content:center}

/* services */
.services{left:0;top:1160px;width:1200px;height:551px;background:linear-gradient(90deg,#0f1113 0%,#22262a 50%,#101214 100%)}
.services-title{left:107px;top:1228px;width:600px;text-align:center;font-family:"Poppins",Arial,sans-serif;font-weight:600;font-size:38px;color:#fff}
.service{width:260px;text-align:center;color:#fff;font-family:"Poppins",Arial,sans-serif;font-weight:600;font-size:17px}
.service svg{display:block;margin:0 auto 14px}
.timetable{left:771px;top:1242px;width:336px;height:415px;background:#fff;padding:36px 20px 0}
.timetable h3{font-family:"Poppins",Arial,sans-serif;font-weight:600;color:var(--red);font-size:23px;line-height:28px;text-align:center}
.timetable p{font-size:14px;line-height:24px;text-align:center;margin:20px 0 18px;color:#222}
.tt-row{display:flex;justify-content:space-between;font-size:14px;line-height:29px;padding:0 6px}
.tt-row b{font-weight:400;color:var(--red);width:110px}
.tt-btn{left:73px;bottom:42px;width:190px;height:40px;font-size:14px}

/* goal + tips */
.circle-photo{border-radius:50%;border:3px solid #111}
.tips{left:0;top:2155px;width:1200px;height:433px;background:var(--soft)}

/* tutorials */
.tut-band{left:0;top:2588px;width:1200px;height:392px;background:linear-gradient(90deg,#3d4a2c 0%,#5e4630 35%,#6a4c3a 65%,#4d3b2c 100%)}
.tut-band::after{content:"";position:absolute;inset:0;background:rgba(0,0,0,.35)}
.tut-title{left:0;top:2675px;width:1200px;text-align:center;font-family:"Poppins",Arial,sans-serif;font-weight:600;font-size:38px;color:#fff;z-index:2}
.video{left:176px;top:2790px;width:830px;height:394px;background:linear-gradient(160deg,#8c9aa7 0%,#5b6d7e 50%,#3c4c5c 100%);z-index:2}
.quote{left:170px;top:3252px;width:860px;text-align:center;font-style:italic;font-size:23px;line-height:36px;color:#111}

/* footer */
.footer{left:0;top:3437px;width:1200px;height:554px;background:linear-gradient(90deg,#121416 0%,#1f2326 50%,#121416 100%)}
.f-col{top:3612px;color:#fff}
.f-col h4{font-family:"Poppins",Arial,sans-serif;font-weight:600;font-size:21px;margin-bottom:22px}
.f-col li{list-style:none;font-size:15px;line-height:34px}
.contact-item{display:flex;gap:14px;font-size:15px;line-height:27px;margin-bottom:12px}
.contact-item svg{flex:none;margin-top:5px}
.copy{left:93px;top:3932px;color:#fff;font-size:15px}
.social{right:96px;top:3928px;display:flex;gap:18px}
.social span{width:26px;height:26px;background:#fff;border-radius:3px}
</style>
</head>
<body>

<!-- Hero -->
<div class="abs hero" role="img" aria-label="Photo of wooden blocks printed with medical symbols: a cross, a heart rate line, a syringe, a stethoscope and a bandage"></div>
<div class="abs hero-shade"></div>
<div class="abs brand brand-top"><span class="brand-dot"></span>Velmora</div>
<div class="abs lang">
  <span class="lang-flag"></span>
  <svg width="16" height="10" viewBox="0 0 16 10"><path d="M2 2l6 6 6-6" fill="none" stroke="#fff" stroke-width="2"/></svg>
</div>
<div class="abs login-btn">Member Login</div>
<nav class="abs nav"><span>Home</span><span>About Us</span><span>Our Services</span><span>Our Goal</span><span>Help</span><span>Contact Us</span></nav>
<h1 class="abs hero-title">Welcome to Velmora</h1>
<p class="abs hero-sub">Lorem Ipsum is simply dummy text of the printing and typesetting industry. Lorem Ipsum has been the industry's standard dummy</p>
<div class="abs search"><span>Find a doctor</span><div class="abs search-btn">Search</div></div>

<!-- About -->
<div class="abs about-photo" role="img" aria-label="Photo of a senior doctor in a white coat with a stethoscope"></div>
<h2 class="abs h-red" style="left:474px;top:740px">About Us</h2>
<p class="abs body-text" style="left:482px;top:834px;width:610px;font-size:14.5px;line-height:26px">Lorem Ipsum is simply dummy text of the printing and typesetting industry. Lorem Ipsum has been the industry's standard dummy text ever since the 1500s, when an unknown printer took a galley of type and scrambled it to make a type specimen book .It has survived not only five centuries, but also the leap into electronic typesetting, remaining essentially unchanged.</p>
<div class="abs btn-red" style="left:482px;top:1011px;width:143px;height:40px">Read More</div>

<!-- Services -->
<div class="abs services" role="img" aria-label="Dark photo of a doctor holding a tablet with floating medical icons"></div>
<h2 class="abs services-title">Our Services</h2>
<div class="abs service" style="left:134px;top:1336px">
  <svg width="96" height="84" viewBox="0 0 96 84" fill="none" stroke="#fff" stroke-width="4"><rect x="6" y="18" width="84" height="60" rx="8"/><path d="M34 18V8h28v10"/><path d="M48 34v28M34 48h28"/></svg>
  Hospitalization Services</div>
<div class="abs service" style="left:437px;top:1336px">
  <svg width="96" height="84" viewBox="0 0 96 84" fill="none" stroke="#fff" stroke-width="4"><path d="M48 78 12 44C0 32 6 8 26 8c10 0 18 6 22 14 4-8 12-14 22-14 20 0 26 24 14 36Z"/><path d="M14 44h20l6-12 10 22 8-16 5 6h20"/></svg>
  Medical Counseling</div>
<div class="abs service" style="left:134px;top:1522px">
  <svg width="96" height="84" viewBox="0 0 96 84" fill="none" stroke="#fff" stroke-width="4"><path d="M8 60c0-14 18-22 40-22s40 8 40 22v10H66V60H30v10H8Z"/><circle cx="48" cy="24" r="20"/><text x="48" y="31" text-anchor="middle" font-family="Poppins,Arial,sans-serif" font-size="18" font-weight="600" fill="#fff" stroke="none">24</text></svg>
  Emergency Services</div>
<div class="abs service" style="left:437px;top:1522px">
  <svg width="96" height="84" viewBox="0 0 96 84" fill="none" stroke="#fff" stroke-width="4"><rect x="10" y="30" width="76" height="50"/><circle cx="48" cy="16" r="12"/><path d="M48 10v12M42 16h12"/><path d="M20 42h10M43 42h10M66 42h10M20 56h10M66 56h10M42 80V60h12v20"/></svg>
  Health Facility</div>
<div class="abs timetable">
  <h3>Check Our<br>Weekly Timetable</h3>
  <p>Suspendisse potenti. Maecenas dapibus ac tellus sed pulvinar. Vestibulum bib volutpat accumsan non laoreet nulla luctus...</p>
  <div class="tt-row"><span>Monday - Friday</span><b>8.00 – 18.00</b></div>
  <div class="tt-row"><span>Saturday</span><b>8.00 – 18.00</b></div>
  <div class="tt-row"><span>Sunday</span><b>8.00 – 18.00</b></div>
  <div class="abs btn-red tt-btn">See Doctors Timetable</div>
</div>

<!-- Our Goal -->
<div class="abs circle-photo" style="left:125px;top:1776px;width:336px;height:336px;background:linear-gradient(135deg,#d9dde2 0%,#6b7380 55%,#2f3540 100%)" role="img" aria-label="Photo of a smiling medical team with a businessman and a nurse holding a clipboard"></div>
<h2 class="abs h-red" style="left:577px;top:1790px">Our Goal</h2>
<p class="abs body-text" style="left:580px;top:1884px;width:512px;font-size:17px;line-height:36px">Lorem Ipsum is simply dummy text of the printing and typesetting industry. Lorem Ipsum has been the industry's standard dummy text ever since the 1500s, when an unknown printer took a galley of type and scrambled it to make a type specimen book</p>

<!-- Health Tips -->
<div class="abs tips"></div>
<h2 class="abs h-red" style="left:93px;top:2220px">Health Tips</h2>
<p class="abs body-text" style="left:93px;top:2310px;width:520px;font-size:17px;line-height:36px">Lorem Ipsum is simply dummy text of the printing and typesetting industry. Lorem Ipsum has been the industry's standard dummy text ever since the 1500s, when an unknown printer took a galley of type and scrambled it to make a type specimen book</p>
<div class="abs circle-photo" style="left:768px;top:2192px;width:336px;height:336px;background:linear-gradient(135deg,#efe9e1 0%,#bfb2a2 55%,#6d6258 100%)" role="img" aria-label="Photo of a doctor consulting with a patient at a desk with a laptop"></div>

<!-- Helpful Tips And Tutorials -->
<div class="abs tut-band" role="img" aria-label="Photo of healthy food: leafy greens, salmon, nuts and grains on a table"></div>
<h2 class="abs tut-title">Helpful Tips And Tutorials</h2>
<div class="abs video" role="img" aria-label="Video preview of a doctor with a stethoscope and floating healthcare icons"></div>
<svg class="abs" style="left:541px;top:2937px;z-index:3" width="100" height="100" viewBox="0 0 100 100"><circle cx="50" cy="50" r="44" fill="none" stroke="#fff" stroke-width="8"/><path d="M40 30 70 50 40 70Z" fill="#fff"/></svg>
<p class="abs quote">Lorem Ipsum is simply dummy text of the printing and typesetting industry. Lorem Ipsum has been the industry's standard dummy text ever since the 1500s, when an unknown printer took a galley of type</p>

<!-- Footer -->
<div class="abs footer"></div>
<div class="abs brand brand-footer"><span class="brand-dot"></span>Velmora</div>
<div class="abs f-col" style="left:93px">
  <h4>Contact Us</h4>
  <div class="contact-item"><svg width="18" height="22" viewBox="0 0 18 22"><path d="M9 1a8 8 0 0 0-8 8c0 6 8 12 8 12s8-6 8-12a8 8 0 0 0-8-8Z" fill="#fff"/><circle cx="9" cy="9" r="3" fill="#1a1c1e"/></svg><span>217 Harrowgate Ln<br>Fernbridge, NH 03990</span></div>
  <div class="contact-item"><svg width="18" height="18" viewBox="0 0 18 18"><path d="M4 1 7 5 5 7c1 2 4 5 6 6l2-2 4 3-2 3C9 17 1 9 1 3Z" fill="#fff"/></svg><span>+1300 555 014</span></div>
  <div class="contact-item" style="margin-top:10px"><svg width="20" height="16" viewBox="0 0 20 16" fill="none" stroke="#fff" stroke-width="2"><rect x="1" y="1" width="18" height="14"/><path d="m1 1 9 8 9-8"/></svg><span>hello@velmora-care.net</span></div>
</div>
<div class="abs f-col" style="left:375px">
  <h4>Quick Links</h4>
  <ul><li>Home</li><li>About Us</li><li>Our Services</li><li>Our Goal</li><li>Help Section</li><li>Contact Us</li></ul>
</div>
<div class="abs f-col" style="left:590px">
  <h4>Helpful Links</h4>
  <ul><li>Provide Comprehensive</li><li>Short-termHospitalization</li><li>Emergency room services</li><li>Laboratory Services</li><li>Blood Services</li></ul>
</div>
<div class="abs f-col" style="left:878px">
  <h4>Glossary</h4>
  <ul><li>Anesthesiology &amp; Pain</li><li>Management Cancer</li><li>(Marlowe) Children's</li><li>Dermatology &amp; Plastic Surgery</li><li>Digestive Disease</li><li>Endocrinology &amp; Metabolis</li></ul>
</div>
<div class="abs copy">© Velmora 2019. All rights reserved</div>
<div class="abs social"><span></span><span></span><span></span><span></span></div>

</body>
</html>
```